Web Design For Marlow Pool Service

We are working with a company that wants a website for their pool service. Some sites to use for content/competitors and inspiration:
https://sacramento.brightwaterpoolco.example/builder/newbuild/repair/ppc
https://hollowbrookpoolcareplus.example/
https://lakemontpoolservice.example/
https://www.dravenspoolresurfacing.example/pool-renovation-ga/
Thank you for taking the time to consider designing a website for us. We are web developers based in Stockton, CA, USA. Most of our projects go through the same process. Understanding this process may help you win a project with us. We custom-code all of our websites in-house. We don’t have any requirements as to what tools you use for your design, but we prefer Figma files. For any design that we label as four-stars, we send it to the client for review. The client picks the final design they want us to use. Once we complete this process, we will continue to show additional clients all the four-star sites and purchase them later. Your designs will have multiple chances to sell. For better chances of success, we ask that you follow these guidelines.
IMAGES:
If you use any images or icons in the design, we ask that you have a link to the asset so we can purchase the image/icon. Most of the designs we submit do not have the customer’s images on them unless they have some great images. Be creative; show us the feeling you are trying to portray with your image choices. Use any royalty-free site you choose. We subscribe to Adobe and mainly use their images, but we can purchase images outside of Adobe. PLEASE NOTE: we will not submit designs to clients with watermarks on the images.
FONTS:
We ask that you identify the fonts used in the design. This can be done in a message if you want. We typically use Google Fonts and Adobe Fonts.
CONTENT:
We're always open to different content and ideas. We often submit designs with stock images so the client can see our vision. We typically take pictures after the website launch to use their images with our vision. Lorem Ipsum is fine for paragraphs, but we ask that you write the headers in correct English. We want to be able to show the vision and identify the sections of the website.
INSPIRATION:
We typically add a couple of links in the brief of websites we like to help you get started in your design.
REVISIONS:
We do not often ask for revisions of the designs unless we see something in the design that may not appeal to the client. If there are slight changes that we want to make, we do that in the development process.
FEEDBACK:
We rarely give feedback on designs during the design process. We are working on many website projects and do not have the time to provide feedback. We usually respond if your request is well thought out and asks specific questions, but a note asking “feedback, please” usually goes unanswered.
Number of Pages Required
1 page
Look and feel
Each slider illustrates characteristics of the customer's brand and the style your logo design should communicate.

```html
<!DOCTYPE html>
<html lang="en">
<head>
<meta charset="utf-8">
<title>Marlow Pool Service</title>
<link href="https://fonts.googleapis.com/css2?family=Signika:wght@500;600&family=Montserrat:wght@400;500;600;700&display=swap" rel="stylesheet">
<style>
:root{
  --navy:#1c3a6c;
  --navy-dark:#1a3358;
  --bar:#1e3560;
  --blue:#2196f3;
  --sky:#3aa0f0;
  --light:#f5f7fa;
  --panel:#edf2f7;
  --text:#2a3550;
  --muted:#6b7487;
  --white:#ffffff;
  --star:#f5b82e;
}
*{margin:0;padding:0;box-sizing:border-box}
html,body{width:1200px;height:4317px;overflow:hidden}
body{position:relative;background:var(--white);font-family:"Montserrat",sans-serif;color:var(--text)}
.abs{position:absolute}
.heading{font-family:"Signika",sans-serif;font-weight:600;color:var(--navy);letter-spacing:.5px}
.eyebrow{position:absolute;font-size:11px;font-weight:700;color:var(--blue);letter-spacing:.5px;display:flex;align-items:center;gap:14px}
.eyebrow::after{content:"";width:48px;height:2px;background:var(--blue)}
.btn{position:absolute;background:var(--blue);color:var(--white);font-size:13px;font-weight:700;display:flex;align-items:center;justify-content:center;border-radius:3px}
.para{position:absolute;font-size:13px;line-height:24px;color:var(--navy)}
.arrow-btn{position:absolute;width:44px;height:64px;background:var(--white);box-shadow:0 2px 10px rgba(20,40,80,.15);display:flex;align-items:center;justify-content:center}

/* top bar */
.top-bar{left:0;top:0;width:1200px;height:34px;background:var(--bar);color:var(--white);font-size:11px;font-weight:600;display:flex;align-items:center;justify-content:center;gap:6px}
.header{left:0;top:34px;width:1200px;height:110px;background:var(--white)}
.logo{position:absolute;display:flex;align-items:center;gap:10px;font-family:"Signika",sans-serif;font-weight:600;color:var(--navy);font-size:24px}
.logo-dot{width:16px;height:16px;border-radius:50%;background:var(--blue)}
.phone{left:687px;top:57px;font-size:16px;color:var(--navy);display:flex;align-items:center;gap:8px}
.appt{left:857px;top:47px;width:192px;height:42px;font-size:12px;border-radius:0}
.nav{left:0;top:110px;font-size:12px;font-weight:700;color:var(--navy)}
.nav span{position:absolute;white-space:nowrap}
.nav .active{color:var(--blue)}
.nav-underline{left:416px;top:141px;width:58px;height:3px;background:var(--navy)}

/* hero */
.hero{left:0;top:144px;width:1200px;height:702px;overflow:hidden}
.hero-photo{position:absolute;inset:0;background:linear-gradient(100deg,#3c5670 0%,#6f8aa0 30%,#a9b9c3 48%,#6fb6d6 70%,#3f97c4 100%)}
.hero-shade{position:absolute;inset:0;background:linear-gradient(90deg,rgba(20,35,60,.55) 0%,rgba(20,35,60,.15) 55%,rgba(0,0,0,0) 100%)}
.hero-welcome{left:90px;top:198px;color:var(--white);font-size:13px;display:flex;align-items:center;gap:24px}
.hero-welcome::after{content:"";width:46px;height:1px;background:var(--white)}
.hero-title{left:90px;top:222px;font-size:44px;line-height:58px;color:var(--white)}
.hero-text{left:90px;top:356px;width:420px;font-size:13.5px;line-height:21px;color:#e8eef5}
.hero-btn{left:90px;top:469px;width:192px;height:41px}

/* services */
.services{left:0;top:846px;width:1200px;height:701px;background:var(--light)}
.service-card{position:absolute;top:207px;width:322px;height:402px;background:var(--white);box-shadow:0 4px 12px rgba(20,40,80,.08);text-align:center}
.service-photo{height:211px}
.service-icon{position:absolute;left:126px;top:176px;width:70px;height:70px;border-radius:50%;background:var(--navy);display:flex;align-items:center;justify-content:center}
.service-title{position:absolute;top:262px;width:100%;font-family:"Signika",sans-serif;font-weight:600;color:var(--navy);font-size:24px}
.service-text{position:absolute;top:304px;left:30px;right:30px;font-size:12.5px;line-height:24px;color:var(--text)}
.service-line{position:absolute;top:372px;left:141px;width:40px;height:2px;background:var(--blue)}

/* quality */
.feature{position:absolute;width:250px}
.feature-title{position:absolute;left:37px;top:0;font-size:14px;font-weight:700;color:var(--navy);white-space:nowrap}
.feature-text{position:absolute;left:40px;top:22px;width:200px;font-size:12.5px;line-height:24px;color:var(--navy)}
.feature-icon{position:absolute;left:0;top:0}

/* about */
.about-panel{left:592px;top:2254px;width:608px;height:399px;background:var(--panel)}
.about-photo{left:0;top:2231px;width:590px;height:447px;border:4px solid var(--sky);background:linear-gradient(135deg,#5aa9d8 0%,#9bbac9 40%,#b8a89a 62%,#c94a45 82%,#8a6c5c 100%)}

/* testimonials */
.quote-card{position:absolute;top:2911px;width:320px;height:240px;background:var(--panel);border-radius:22px}
.quote-mark{position:absolute;left:0;top:-20px}
.stars{position:absolute;left:32px;top:40px;color:var(--star);font-size:15px;letter-spacing:2px}
.quote-title{position:absolute;left:32px;top:66px;font-size:15px;font-weight:700;color:#151d2e}
.quote-text{position:absolute;left:32px;top:96px;width:268px;font-size:12px;line-height:24px;color:#151d2e}
.client{position:absolute;top:3191px;display:flex;align-items:center;gap:12px}
.avatar{width:44px;height:44px;border-radius:50%;background:linear-gradient(135deg,#c8b8a8,#6e6258)}
.client-name{font-family:"Signika",sans-serif;font-weight:600;color:var(--blue);font-size:17px}
.client-role{font-size:11px;color:var(--text)}

/* contact */
.contact{left:0;top:3313px;width:1200px;height:1004px;background:var(--light)}
.field{position:absolute;background:var(--white);border:1px solid #e1e6ee;font-size:11px;color:#8a93a3;padding:0 16px;display:flex;align-items:center}
.field.area{align-items:flex-start;padding-top:14px}
.contact-photo{left:608px;top:84px;width:486px;height:396px;background:linear-gradient(150deg,#2fc3e0 0%,#1aa5d2 50%,#128cbd 78%,#c49c78 100%)}

/* footer */
.footer{left:0;top:3840px;width:1200px;height:477px}
.footer-body{position:absolute;left:0;top:100px;width:1200px;height:377px;background:var(--navy-dark)}
.footer-head{position:absolute;font-size:14px;font-weight:700;color:var(--white)}
.footer-row{position:absolute;display:flex;gap:16px;font-size:11px;line-height:21px;color:var(--white)}
.hours{position:absolute;right:94px;display:flex;align-items:center;gap:18px;font-size:11px;color:var(--white)}
.social{position:absolute;top:4185px;width:37px;height:37px;border:1px solid rgba(255,255,255,.8)}
.footer-line{left:62px;top:4267px;width:1078px;height:1px;background:rgba(255,255,255,.25)}
.copyright{left:0;top:4283px;width:1200px;text-align:center;font-size:12px;color:var(--white)}
</style>
</head>
<body>

<div class="abs top-bar">
  <svg width="10" height="13" viewBox="0 0 10 13"><path d="M5 0.5a4.3 4.3 0 0 0-4.3 4.3C0.7 8 5 12.5 5 12.5S9.3 8 9.3 4.8A4.3 4.3 0 0 0 5 0.5z" fill="none" stroke="#fff" stroke-width="1.2"/><circle cx="5" cy="4.8" r="1.5" fill="#fff"/></svg>
  6015 Some place somewhere
</div>

<header class="abs header">
  <div class="logo" style="left:95px;top:30px"><span class="logo-dot"></span>Marlow Pool Service</div>
</header>
<div class="abs phone">
  <svg width="16" height="16" viewBox="0 0 24 24"><path d="M6.6 10.8a15 15 0 0 0 6.6 6.6l2.2-2.2a1 1 0 0 1 1-.25 11.4 11.4 0 0 0 3.6.57 1 1 0 0 1 1 1V20a1 1 0 0 1-1 1A17 17 0 0 1 3 4a1 1 0 0 1 1-1h3.5a1 1 0 0 1 1 1c0 1.25.2 2.45.57 3.57a1 1 0 0 1-.25 1z" fill="#1c3a6c"/></svg>
  (000) 123-4567
</div>
<div class="btn appt">REQUEST APPOINTMENT</div>
<nav class="abs nav">
  <span class="active" style="left:422px">HOME</span>
  <span style="left:513px">ABOUT US</span>
  <span style="left:637px">SERVICES</span>
  <span style="left:756px">OUR TEAM</span>
  <span style="left:887px">GALLERY</span>
  <span style="left:1004px">CONTACT US</span>
</nav>
<div class="abs nav-underline"></div>

<section class="abs hero">
  <div class="hero-photo" role="img" aria-label="Children running toward a sunlit swimming pool carrying inflatable rings"></div>
  <div class="hero-shade"></div>
  <div class="abs hero-welcome">Welcome</div>
  <h1 class="abs heading hero-title" style="color:#fff">Crafting Memories,<br>One Pool at a Time</h1>
  <p class="abs hero-text">Lorem ipsum dolor sit amet, consectetur adipiscing elit, sed do eiusmod tempor incididunt ut labore et dolore magna Lorem ipsum dolor sit amet, consectetur adipiscing elit, sed do eiusmod tempor incididunt ut labore et dolore magna</p>
  <div class="btn hero-btn">Discover more</div>
  <svg class="abs" style="left:0;top:0" width="1200" height="702" viewBox="0 0 1200 702">
    <path d="M0 620 Q600 840 1200 560 L1200 702 L0 702 Z" fill="#f5f7fa"/>
    <path d="M0 612 Q600 850 1200 548" fill="none" stroke="#1c3a6c" stroke-width="9"/>
    <path d="M0 600 Q600 830 1200 530" fill="none" stroke="#2196f3" stroke-width="7"/>
    <path d="M200 676 Q700 760 1200 570" fill="none" stroke="#1c3a6c" stroke-width="6"/>
  </svg>
</section>

<section class="abs services">
  <div class="eyebrow" style="left:100px;top:80px">OUR TREATMENTS</div>
  <h2 class="abs heading" style="left:97px;top:114px;font-size:46px">Services We Provide</h2>
  <div class="arrow-btn" style="left:1011px;top:96px"><svg width="10" height="16"><path d="M8 2 2 8l6 6" fill="none" stroke="#111" stroke-width="1.8"/></svg></div>
  <div class="arrow-btn" style="left:1063px;top:96px"><svg width="10" height="16"><path d="M2 2l6 6-6 6" fill="none" stroke="#111" stroke-width="1.8"/></svg></div>

  <div class="service-card" style="left:94px">
    <div class="service-photo" role="img" aria-label="Technician scrubbing blue pool tiles" style="background:linear-gradient(135deg,#3a8fc6,#7fc1e3 60%,#2c6a9c)"></div>
    <div class="service-icon"><svg width="30" height="30" viewBox="0 0 24 24"><path d="M12 2l2.6 3.2 4-.6-.6 4L21 12l-3 2.4.6 4-4-.6L12 22l-2.6-3.2-4 .6.6-4L3 12l3-2.4-.6-4 4 .6z" fill="none" stroke="#fff" stroke-width="1.4"/></svg></div>
    <div class="service-title">Pool Cleaning</div>
    <div class="service-text">Lorem ipsum dolor sit amet, consectetur adi piscing elit sed do eiusmod tmpor</div>
    <div class="service-line"></div>
  </div>
  <div class="service-card" style="left:442px">
    <div class="service-photo" role="img" aria-label="Construction crew in hard hats at a pool build site" style="background:linear-gradient(135deg,#c9d2d8,#8ea3b0 50%,#b8c44a 80%,#6d7a52)"></div>
    <div class="service-icon"><svg width="30" height="30" viewBox="0 0 24 24"><path d="M5 19h14M8 19l4-12 4 12M10 13h4" fill="none" stroke="#fff" stroke-width="1.5"/></svg></div>
    <div class="service-title">Pool Construction</div>
    <div class="service-text">Lorem ipsum dolor sit amet, consectetur adi piscing elit sed do eiusmod tmpor</div>
    <div class="service-line"></div>
  </div>
  <div class="service-card" style="left:791px">
    <div class="service-photo" role="img" aria-label="Family relaxing on floats in a bright outdoor pool" style="background:linear-gradient(160deg,#9a8e72,#55c4d8 40%,#2fb4d6 75%,#a9784e)"></div>
    <div class="service-icon"><svg width="30" height="30" viewBox="0 0 24 24"><circle cx="12" cy="8" r="3" fill="none" stroke="#fff" stroke-width="1.4"/><circle cx="6" cy="10" r="2" fill="none" stroke="#fff" stroke-width="1.4"/><circle cx="18" cy="10" r="2" fill="none" stroke="#fff" stroke-width="1.4"/><path d="M6 19c0-3.3 2.7-6 6-6s6 2.7 6 6M2 18c0-2.2 1.8-4 4-4M22 18c0-2.2-1.8-4-4-4" fill="none" stroke="#fff" stroke-width="1.4"/></svg></div>
    <div class="service-title">Pool Repair</div>
    <div class="service-text">Lorem ipsum dolor sit amet, consectetur adi piscing elit sed do eiusmod tmpor</div>
    <div class="service-line"></div>
  </div>
</section>

<section>
  <div class="eyebrow" style="left:97px;top:1632px">TREATMENTS</div>
  <h2 class="abs heading" style="left:95px;top:1664px;font-size:48px;line-height:61px">Quality Pools,<br>Superior Service</h2>
  <p class="para" style="left:97px;top:1798px;width:460px">Lorem ipsum dolor sit amet, consectetur adipiscing elit, sed do eiusmo empor incididunt ut abore et dolore magna aliqua. Ut enim ad minim iam, quis nostrud exercitation ullamco</p>

  <div class="feature" style="left:106px;top:1902px">
    <svg class="feature-icon" width="30" height="30" viewBox="0 0 24 24"><circle cx="12" cy="12" r="3" fill="none" stroke="#2196f3" stroke-width="1.3"/><path d="M12 3l1.6 2.3 2.7-.6.6 2.7L19.2 9l-.9 2.6 1.2 2.5-2.5 1.2-.3 2.8-2.8-.2L12 20l-1.9-2.1-2.8.2-.3-2.8-2.5-1.2 1.2-2.5L4.8 9l2.3-1.6.6-2.7 2.7.6z" fill="none" stroke="#2196f3" stroke-width="1.3"/></svg>
    <div class="feature-title">Quality Assurance</div>
    <div class="feature-text">Lorem ipsum dolor sit amet, consectetur adipiscing</div>
  </div>
  <div class="feature" style="left:379px;top:1902px">
    <svg class="feature-icon" width="30" height="30" viewBox="0 0 24 24"><circle cx="11" cy="11" r="8" fill="none" stroke="#2196f3" stroke-width="1.3"/><circle cx="17" cy="17" r="3.5" fill="#fff" stroke="#2196f3" stroke-width="1.3"/><path d="M5 9h6M8 6v8" stroke="#2196f3" stroke-width="1.3"/></svg>
    <div class="feature-title">Professional</div>
    <div class="feature-text">Lorem ipsum dolor sit amet, consectetur adipiscing</div>
  </div>
  <div class="feature" style="left:106px;top:2000px">
    <svg class="feature-icon" width="30" height="30" viewBox="0 0 24 24"><circle cx="12" cy="8" r="4" fill="none" stroke="#2196f3" stroke-width="1.3"/><path d="M4 21c0-4.4 3.6-7 8-7s8 2.6 8 7z" fill="none" stroke="#2196f3" stroke-width="1.3"/></svg>
    <div class="feature-title">Comprehensive Services</div>
    <div class="feature-text">Lorem ipsum dolor sit amet, consectetur adipiscing</div>
  </div>
  <div class="feature" style="left:379px;top:2000px">
    <svg class="feature-icon" width="30" height="30" viewBox="0 0 24 24"><path d="M12 3l2.7 5.6 6.1.9-4.4 4.3 1 6.1L12 17l-5.4 2.9 1-6.1-4.4-4.3 6.1-.9z" fill="none" stroke="#2196f3" stroke-width="1.3"/></svg>
    <div class="feature-title">Client-centric</div>
    <div class="feature-text">Lorem ipsum dolor sit amet, consectetur adipiscing</div>
  </div>
  <div class="btn" style="left:104px;top:2112px;width:168px;height:44px">Apply Now</div>

  <svg class="abs" style="left:640px;top:1652px" width="476" height="476" viewBox="0 0 476 476">
    <path d="M20 232 A218 218 0 1 1 238 450" fill="none" stroke="#1c3a6c" stroke-width="6"/>
  </svg>
  <div class="abs" role="img" aria-label="Woman in a sun hat lounging on a pink flamingo float in clear blue water" style="left:654px;top:1667px;width:446px;height:446px;border-radius:50%;background:radial-gradient(circle at 50% 45%,#f08bb0 0%,#e7749e 22%,#5cb6e6 40%,#2e8fd0 75%,#1f74b8 100%)"></div>
</section>

<section>
  <div class="abs about-panel"></div>
  <div class="abs about-photo" role="img" aria-label="Pool technician in a red cap repairing equipment beside the pool deck"></div>
  <div class="eyebrow" style="left:649px;top:2296px">ABOUT US</div>
  <h2 class="abs heading" style="left:647px;top:2327px;font-size:48px;line-height:61px">Crafting Aquatic<br>Masterpieces</h2>
  <p class="para" style="left:649px;top:2462px;width:460px">Lorem ipsum dolor sit amet, consectetur adipiscing elit, sed do eiusmo empor incididunt ut abore et dolore magna aliqua. Ut enim ad minim iam, quis nostrud exercitation ullamco</p>
  <div class="btn" style="left:649px;top:2564px;width:167px;height:46px">Apply Now</div>
</section>

<section>
  <div class="eyebrow" style="left:96px;top:2765px">TESTIMONIALS</div>
  <h2 class="abs heading" style="left:92px;top:2798px;font-size:48px">What Clients Are Saying</h2>
  <div class="arrow-btn" style="left:1004px;top:2779px"><svg width="10" height="16"><path d="M8 2 2 8l6 6" fill="none" stroke="#111" stroke-width="1.8"/></svg></div>
  <div class="arrow-btn" style="left:1058px;top:2779px"><svg width="10" height="16"><path d="M2 2l6 6-6 6" fill="none" stroke="#111" stroke-width="1.8"/></svg></div>

  <div class="quote-card" style="left:92px">
    <svg class="quote-mark" style="left:30px" width="52" height="36" viewBox="0 0 52 36"><path d="M0 36V14L10 0h10L12 14h10v22zM28 36V14L38 0h10L40 14h10v22z" fill="#2196f3"/></svg>
    <div class="stars">★★★★★</div>
    <div class="quote-title">They are the Best</div>
    <div class="quote-text">Lorem ipsum dolor sit amet, consectetur adipiscing elit, sed do eiusmod tempor i ncididunt ut labore et dolore magna aliqua. Ut enim ad minim veniam, quis nostrud exercitation ullamco laboris nisi ut</div>
  </div>
  <div class="quote-card" style="left:439px">
    <svg class="quote-mark" style="left:30px" width="52" height="36" viewBox="0 0 52 36"><path d="M0 36V14L10 0h10L12 14h10v22zM28 36V14L38 0h10L40 14h10v22z" fill="#2196f3"/></svg>
    <div class="stars">★★★★★</div>
    <div class="quote-title">They are the Best</div>
    <div class="quote-text">Lorem ipsum dolor sit amet, consectetur adipiscing elit, sed do eiusmod tempor i ncididunt ut labore et dolore magna aliqua. Ut enim ad minim veniam, quis nostrud exercitation ullamco laboris nisi ut</div>
  </div>
  <div class="quote-card" style="left:784px">
    <svg class="quote-mark" style="left:30px" width="52" height="36" viewBox="0 0 52 36"><path d="M0 36V14L10 0h10L12 14h10v22zM28 36V14L38 0h10L40 14h10v22z" fill="#2196f3"/></svg>
    <div class="stars">★★★★★</div>
    <div class="quote-title">They are the Best</div>
    <div class="quote-text">Lorem ipsum dolor sit amet, consectetur adipiscing elit, sed do eiusmod tempor i ncididunt ut labore et dolore magna aliqua. Ut enim ad minim veniam, quis nostrud exercitation ullamco laboris nisi ut</div>
  </div>

  <div class="client" style="left:125px"><div class="avatar" role="img" aria-label="Client portrait"></div><div><div class="client-name">Jessica</div><div class="client-role">CEO, Abc Company</div></div></div>
  <div class="client" style="left:472px"><div class="avatar" role="img" aria-label="Client portrait"></div><div><div class="client-name">Jessica</div><div class="client-role">CEO, Abc Company</div></div></div>
  <div class="client" style="left:817px"><div class="avatar" role="img" aria-label="Client portrait"></div><div><div class="client-name">Jessica</div><div class="client-role">CEO, Abc Company</div></div></div>
</section>

<section class="abs contact">
  <div class="eyebrow" style="left:136px;top:72px">GET IN TOUCH</div>
  <h2 class="abs heading" style="left:133px;top:104px;font-size:48px">Contact Us</h2>
  <div class="abs" style="left:138px;top:176px;font-size:11.5px;color:var(--text)">Just send a message, we will answer within 24 hours</div>
  <div class="field" style="left:134px;top:232px;width:198px;height:37px">Your full name</div>
  <div class="field" style="left:354px;top:232px;width:197px;height:37px">Phone Number</div>
  <div class="field" style="left:134px;top:284px;width:198px;height:35px">Mail Address</div>
  <div class="field" style="left:354px;top:284px;width:197px;height:35px">Subject</div>
  <div class="field area" style="left:134px;top:334px;width:417px;height:87px">Type your message...</div>
  <div class="btn" style="left:134px;top:445px;width:417px;height:35px;font-size:11px">Send Your Message</div>
  <div class="abs contact-photo" role="img" aria-label="Woman in a straw hat sitting at the edge of a turquoise pool"></div>
</section>

<footer class="abs footer">
  <svg class="abs" style="left:0;top:0" width="1200" height="110" viewBox="0 0 1200 110">
    <path d="M0 110 L0 70 Q500 -40 1200 80 L1200 110 Z" fill="#1a3358"/>
    <path d="M0 62 Q500 -50 1200 70" fill="none" stroke="#1c3a6c" stroke-width="8"/>
    <path d="M0 54 Q500 -58 1200 58" fill="none" stroke="#2196f3" stroke-width="6"/>
    <path d="M700 8 Q1000 20 1200 95" fill="none" stroke="#2196f3" stroke-width="5"/>
  </svg>
  <div class="footer-body"></div>
</footer>
<div class="logo" style="left:490px;top:4006px;color:#fff"><span class="logo-dot"></span>Marlow Pool Service</div>

<div class="footer-head" style="left:94px;top:4056px">CONTACT US</div>
<div class="footer-row" style="left:94px;top:4094px">
  <svg width="12" height="16" viewBox="0 0 10 13"><path d="M5 .5a4.3 4.3 0 0 0-4.3 4.3C.7 8 5 12.5 5 12.5S9.3 8 9.3 4.8A4.3 4.3 0 0 0 5 .5z" fill="#fff"/><circle cx="5" cy="4.8" r="1.5" fill="#1a3358"/></svg>
  <span style="width:180px">101- lorem ipsum simple text print type text industry text.</span>
</div>
<div class="footer-row" style="left:94px;top:4154px">
  <svg width="14" height="14" viewBox="0 0 24 24"><path d="M6.6 10.8a15 15 0 0 0 6.6 6.6l2.2-2.2a1 1 0 0 1 1-.25 11.4 11.4 0 0 0 3.6.57 1 1 0 0 1 1 1V20a1 1 0 0 1-1 1A17 17 0 0 1 3 4a1 1 0 0 1 1-1h3.5a1 1 0 0 1 1 1c0 1.25.2 2.45.57 3.57a1 1 0 0 1-.25 1z" fill="#fff"/></svg>
  <span>123 456 7890</span>
</div>
<div class="footer-row" style="left:94px;top:4191px">
  <svg width="16" height="12" viewBox="0 0 16 12"><rect width="16" height="12" fill="#fff"/><path d="M0 0l8 6 8-6" fill="none" stroke="#1a3358" stroke-width="1.3"/></svg>
  <span>info@company.com</span>
</div>

<div class="abs" style="left:450px;top:4102px;width:300px;text-align:center;font-size:11px;line-height:21px;color:#fff">Lorem ipsum dolor sit amet, consectetur adipisc ing elit, sed do eiusmod tempor incididunt bbbbbut bcbbcbnmx zjzmsmmzm</div>
<div class="social" style="left:536px"></div>
<div class="social" style="left:580px"></div>
<div class="social" style="left:625px"></div>

<div class="footer-head" style="right:94px;top:4056px">OPENING HOURS</div>
<div class="hours" style="top:4101px">Mon - Fri: 9am - to - 6pm <svg width="16" height="16" viewBox="0 0 16 16"><circle cx="8" cy="8" r="6.5" fill="none" stroke="#fff" stroke-width="1.2"/><path d="M8 4v4l3 2" fill="none" stroke="#fff" stroke-width="1.2"/></svg></div>
<div class="hours" style="top:4131px">Saturday 9am - to - 2pm <svg width="16" height="16" viewBox="0 0 16 16"><circle cx="8" cy="8" r="6.5" fill="none" stroke="#fff" stroke-width="1.2"/><path d="M8 4v4l3 2" fill="none" stroke="#fff" stroke-width="1.2"/></svg></div>
<div class="hours" style="top:4162px">Sunday : <u>Closed</u> <svg width="16" height="16" viewBox="0 0 16 16"><circle cx="8" cy="8" r="6.5" fill="none" stroke="#fff" stroke-width="1.2"/><path d="M8 4v4l3 2" fill="none" stroke="#fff" stroke-width="1.2"/></svg></div>

<div class="abs footer-line"></div>
<div class="abs copyright">Marlow Pool Services</div>

</body>
</html>
```